Label design for an exciting new Vodka brand

We need a label design for a dynamic new Vodka brand called 'Pale lantern drift Vodka'. It is a crisp and versatile liquid with a clean and smooth finish. It should appeal to 21-39 year olds, with a slight female skew. Colours, fonts and styles should be modern and relatively neutral - take inspiration from the brand pictures attached.

Target Market(s)

21-39 year olds, both male and female, but with a slight female skew

```html
<!DOCTYPE html>
<html lang="en">
<head>
<meta charset="utf-8">
<title>Pale lantern drift Vodka – Label</title>
<link rel="stylesheet" href="https://fonts.googleapis.com/css2?family=Russo+One&display=swap">
<style>
  :root {
    --canvas-bg: #eef1f5;
    --ink: #2d5870;
    --blue-deep: #2a6f98;
    --blue-light: #8cc9e2;
    --steel: #c9cdd1;
  }
  * { margin: 0; padding: 0; box-sizing: border-box; }
  html, body {
    width: 1200px;
    height: 1200px;
    overflow: hidden;
    background: var(--canvas-bg);
  }
  .label {
    position: relative;
    width: 1200px;
    height: 1200px;
  }
  .accent-band {
    position: absolute;
    width: 630px;
    height: 188px;
    border-radius: 6px;
  }
  .accent-band--top {
    left: 278px;
    top: 117px;
    background: linear-gradient(90deg, var(--steel) 0%, var(--blue-light) 20%, var(--blue-deep) 45%, var(--steel) 100%);
  }
  .accent-band--bottom {
    left: 292px;
    top: 895px;
    background: linear-gradient(270deg, var(--steel) 0%, var(--blue-light) 20%, var(--blue-deep) 45%, var(--steel) 100%);
  }
  .wordmark {
    position: absolute;
    left: 0;
    right: 0;
    top: 395px;
    text-align: center;
    font-family: "Russo One", sans-serif;
    font-weight: 400;
    color: var(--ink);
    text-transform: uppercase;
    line-height: 1;
  }
  .wordmark-line { display: block; }
  .wordmark-line--top { font-size: 140px; letter-spacing: 2px; }
  .wordmark-line--middle { font-size: 60px; letter-spacing: 1px; margin-top: 10px; }
  .wordmark-line--bottom { font-size: 122px; letter-spacing: 4px; margin-top: 14px; }
</style>
</head>
<body>
  <main class="label">
    <div class="accent-band accent-band--top" role="img" aria-label="Decorative slanted blue and steel stripe motif"></div>

    <h1 class="wordmark">
      <span class="wordmark-line wordmark-line--top">Pale</span>
      <span class="wordmark-line wordmark-line--middle">Lantern Drift</span>
      <span class="wordmark-line wordmark-line--bottom">Vodka</span>
    </h1>

    <div class="accent-band accent-band--bottom" role="img" aria-label="Decorative slanted blue and steel stripe motif, mirrored"></div>
  </main>
</body>
</html>
```